Business Card Design

New business card design

Target Market(s)

Residential & Commercial Property Managers

Industry/Entity Type

Plumbing Services

Contact Information for Business Card

Name - Rowan Keddle, title - Director, Phone Number - 0431 286 517, email - rowan@tbk-plumbing.com.au, Company ABN - 73 215 904 386,

Font styles to use
Sans Serif

Colors
0054AA
0677BA
7BADD7
CADEEF
E8F1F8

```html
<!DOCTYPE html>
<html lang="en">
<head>
<meta charset="utf-8">
<title>TBK Plumbing Services – Business Card</title>
<link rel="stylesheet" href="https://fonts.googleapis.com/css2?family=Montserrat:wght@400;700&display=swap">
<style>
  :root {
    --sky: #2BA8E0;
    --sky-deep: #0677BA;
    --navy: #1E2530;
    --ink: #1A1D22;
    --paper: #FFFFFF;
    --backdrop: #E8F1F8;
  }
  * { box-sizing: border-box; margin: 0; padding: 0; }
  html, body {
    width: 1200px; height: 900px; overflow: hidden;
    background: var(--backdrop);
    font-family: "Montserrat", sans-serif;
  }
  .sheet {
    position: relative; width: 1200px; height: 900px;
    display: flex; flex-direction: column; align-items: center; justify-content: center; gap: 60px;
  }
  .card {
    position: relative; width: 560px; height: 320px;
    border-radius: 22px; overflow: hidden;
    box-shadow: 0 10px 28px rgba(20, 40, 70, 0.18);
  }
  .card--front { background: var(--sky); display: flex; align-items: center; justify-content: center; }
  .card--front .brand-name {
    font-size: 40px; font-weight: 400; color: var(--sky-deep); letter-spacing: 1px; white-space: nowrap;
  }
  .card--back { background: var(--paper); }
  .card-sweep { position: absolute; inset: 0; width: 560px; height: 320px; }
  .brand-mark {
    position: absolute; top: 44px; right: 36px;
    font-size: 22px; font-weight: 400; color: var(--ink); white-space: nowrap;
  }
  .abn {
    position: absolute; right: 34px; top: 150px;
    font-size: 14px; line-height: 1.35; color: var(--ink); white-space: nowrap;
  }
  .person { position: absolute; left: 150px; top: 176px; white-space: nowrap; }
  .person-name { font-size: 25px; font-weight: 700; color: var(--sky); line-height: 1.2; }
  .person-title { font-size: 16px; color: var(--ink); margin-top: 2px; margin-left: 14px; }
  .contact-list { position: absolute; left: 176px; top: 246px; list-style: none; }
  .contact-list li {
    display: flex; align-items: center; gap: 8px;
    font-size: 16px; color: var(--ink); line-height: 1.55; white-space: nowrap;
  }
  .contact-list svg { width: 14px; height: 14px; flex: none; }
</style>
</head>
<body>
<main class="sheet">
  <section class="card card--front" aria-label="Card front">
    <span class="brand-name">TBK Plumbing Services</span>
  </section>

  <section class="card card--back" aria-label="Card back">
    <svg class="card-sweep" viewBox="0 0 560 320" aria-hidden="true">
      <path d="M0 0 H340 C200 40 70 150 30 320 H0 Z" fill="var(--sky)"/>
      <path d="M340 0 C200 40 70 150 30 320 H42 C86 160 220 48 358 0 Z" fill="var(--navy)"/>
    </svg>

    <p class="brand-mark">TBK Plumbing Services</p>

    <p class="abn">Company ABN<br>- 73 215 904 386</p>

    <div class="person">
      <p class="person-name">Rowan Keddle</p>
      <p class="person-title">Director</p>
    </div>

    <ul class="contact-list">
      <li>
        <svg viewBox="0 0 24 24"><path fill="var(--sky)" d="M6.6 10.8a15 15 0 0 0 6.6 6.6l2.2-2.2c.3-.3.7-.4 1-.2 1.1.4 2.3.6 3.6.6.6 0 1 .4 1 1V20c0 .6-.4 1-1 1A17 17 0 0 1 3 4c0-.6.4-1 1-1h3.5c.6 0 1 .4 1 1 0 1.3.2 2.5.6 3.6.1.3 0 .7-.2 1z"/></svg>
        0431 286 517
      </li>
      <li>
        <svg viewBox="0 0 24 24"><path fill="var(--sky)" d="M2 6a2 2 0 0 1 2-2h16a2 2 0 0 1 2 2v12a2 2 0 0 1-2 2H4a2 2 0 0 1-2-2zm2 .5V7l8 5 8-5v-.5z"/></svg>
        rowan@tbk-plumbing.com.au
      </li>
    </ul>
  </section>
</main>
</body>
</html>
```